Business Card for Coastal Tundrabridge Advisory

We need a business card for Coastal Tundrabridge Advisory. The company website address is provided below. The company logo is attached. We provide specialized permafrost services to the mining, transportation, and oil & gas industries. The card should be prepared for:
Matthias Korhonen, PhD.
Coastal Tundrabridge Advisory
PO Box 418259
Quillwater, Alaska 99642
Direct: +1-907-555-0143
Email: mkorhonen@tundrabridgeadvisory.example
Website: www.coastaltundrabridgeadvisory.example

```html
<!DOCTYPE html>
<html lang="en">
<head>
<meta charset="utf-8">
<title>Coastal Tundrabridge Advisory — Business Card</title>
<link rel="stylesheet" href="https://fonts.googleapis.com/css2?family=Montserrat:wght@400;500;600;800&display=swap">
<style>
  :root {
    --canvas: #2b2b2b;
    --card-black: #111111;
    --card-white: #ffffff;
    --band: #1d202c;
    --ink: #1d202c;
    --ink-light: #f2f2f2;
    --muted: #8c8f99;
    --art: #2a2a2a;
  }
  * { box-sizing: border-box; margin: 0; padding: 0; }
  html, body { width: 1200px; height: 1043px; overflow: hidden; }
  body {
    background: var(--canvas);
    font-family: "Montserrat", sans-serif;
    display: flex;
    align-items: center;
    justify-content: center;
    gap: 60px;
  }
  .card {
    position: relative;
    width: 510px;
    height: 292px;
    border-radius: 4px;
    overflow: hidden;
  }

  /* Front */
  .card-front { background: var(--card-black); }
  .card-front .brand {
    position: absolute;
    left: 80px;
    top: 92px;
    color: var(--ink-light);
    font-weight: 600;
    font-size: 22px;
    letter-spacing: 2px;
    text-transform: uppercase;
    line-height: 1.25;
  }
  .card-front .artwork {
    position: absolute;
    left: 170px;
    top: 150px;
    width: 190px;
    height: 110px;
    background: linear-gradient(180deg, var(--art), #181818);
    border-radius: 2px;
  }

  /* Back */
  .card-back { background: var(--card-white); color: var(--ink); }
  .card-back .brand {
    position: absolute;
    left: 38px;
    top: 34px;
    font-weight: 600;
    font-size: 15px;
    letter-spacing: 1.5px;
    text-transform: uppercase;
    line-height: 1.3;
    color: var(--ink);
  }
  .band {
    position: absolute;
    left: 0;
    right: 0;
    top: 120px;
    height: 92px;
    background: var(--band);
    color: var(--ink-light);
  }
  .holder {
    position: absolute;
    left: 38px;
    top: 26px;
  }
  .holder .name { font-weight: 800; font-size: 15px; letter-spacing: .3px; }
  .holder .company { font-weight: 400; font-size: 12px; margin-top: 5px; }
  .divider {
    position: absolute;
    left: 272px;
    top: 14px;
    bottom: 14px;
    width: 1px;
    background: rgba(255,255,255,.35);
  }
  .contacts {
    position: absolute;
    left: 288px;
    top: 12px;
    list-style: none;
    font-size: 8px;
    line-height: 1.35;
  }
  .contacts li { display: flex; align-items: center; gap: 8px; margin-bottom: 7px; }
  .contacts svg { flex: none; width: 11px; height: 11px; fill: var(--ink-light); }
  .website {
    position: absolute;
    left: 38px;
    top: 234px;
    display: flex;
    align-items: center;
    gap: 8px;
    font-size: 8.5px;
    color: var(--ink);
  }
  .website svg { width: 11px; height: 11px; }
</style>
</head>
<body>

  <section class="card card-front" aria-label="Card front">
    <div class="brand">Coastal Tundrabridge<br>Advisory</div>
    <div class="artwork" role="img" aria-label="Line illustration of an oil pump jack"></div>
  </section>

  <section class="card card-back" aria-label="Card back">
    <div class="brand">Coastal Tundrabridge<br>Advisory</div>

    <div class="band">
      <div class="holder">
        <p class="name">Matthias Korhonen, PhD.</p>
        <p class="company">Coastal Tundrabridge Advisory</p>
      </div>
      <div class="divider"></div>
      <ul class="contacts">
        <li>
          <svg viewBox="0 0 24 24" aria-hidden="true"><path d="M12 2a7 7 0 0 0-7 7c0 5 7 13 7 13s7-8 7-13a7 7 0 0 0-7-7zm0 9.5A2.5 2.5 0 1 1 12 6.5a2.5 2.5 0 0 1 0 5z"/></svg>
          <span>PO Box 418259<br>Quillwater, Alaska 99642</span>
        </li>
        <li>
          <svg viewBox="0 0 24 24" aria-hidden="true"><path d="M6.6 10.8a15 15 0 0 0 6.6 6.6l2.2-2.2a1 1 0 0 1 1-.25 11.4 11.4 0 0 0 3.6.57 1 1 0 0 1 1 1V20a1 1 0 0 1-1 1A17 17 0 0 1 3 4a1 1 0 0 1 1-1h3.5a1 1 0 0 1 1 1c0 1.25.2 2.45.57 3.57a1 1 0 0 1-.25 1z"/></svg>
          <span>+1-907-555-0143</span>
        </li>
        <li>
          <svg viewBox="0 0 24 24" aria-hidden="true"><path d="M3 5h18a1 1 0 0 1 1 1v12a1 1 0 0 1-1 1H3a1 1 0 0 1-1-1V6a1 1 0 0 1 1-1zm9 7.5L4 7.2V8l8 5.3L20 8v-.8z"/></svg>
          <span>mkorhonen@tundrabridgeadvisory.example</span>
        </li>
      </ul>
    </div>

    <div class="website">
      <svg viewBox="0 0 24 24" aria-hidden="true"><circle cx="12" cy="12" r="10" fill="#1d202c"/><path d="M2 12h20M12 2c3 3 3 17 0 20M12 2c-3 3-3 17 0 20" stroke="#fff" stroke-width="1.4" fill="none"/></svg>
      <span>www.coastaltundrabridgeadvisory.example</span>
    </div>
  </section>

</body>
</html>
```